Flat bootstrap design for existing site

I'm looking for a modern flat design based around an existing logo. This has to be a custom design (no external templates), and implemented into a bootstrap framework.

The logo is attached as 2 versions - choose whichever you want, that flows better with whatever design you choose.

Added screenshots of the existing site (currently using the default bootstrap layouts). Please make your designs around those pages in the screenshots (i.e. the homepage only has the postal code input and the header). The active page has 3 screenshots, because I wanted to illustrate the other states that would be visible (in the table rows).

This is a moving/junk removal website, just for some context.

Here's some example websites (flat designs) that I like, just to give you an idea of what I'm after.

https://www.plimvora.com/
https://dacklow.com/
https://trevanu.com/
https://quobrintal.com/en/

Coding

Coded - Design and coding required

Number of Pages Required

5+ page

Colors

Designer to choose colors to be used in the design.

Requirements
Must have
• It must be a modern/simple flat design, that is built around the existing logo (attached).
• It has to be implemented using bootstrap.

```html
<!DOCTYPE html>
<html lang="en">
<head>
<meta charset="utf-8">
<title>Haulvex – Booking Details</title>
<link rel="stylesheet" href="https://fonts.googleapis.com/css2?family=Open+Sans:wght@400;600&family=Raleway:wght@500;600;800&display=swap">
<style>
:root{
  --brand:#4cc8f3;
  --ink:#2e2e2e;
  --muted:#555;
  --page:#eef6fa;
  --line:#8e8e8e;
  --table-head:#72bcdc;
  --notice:#d4edf6;
  --row-alt:#e1eef4;
  --accepted:#74ad58;
  --sent:#70bad9;
  --pending:#7a878d;
}
*{box-sizing:border-box;margin:0;padding:0}
html,body{width:1200px;height:1085px;overflow:hidden}
body{background:var(--page);font-family:"Open Sans",sans-serif;color:var(--ink);position:relative}
.site-header{position:absolute;left:0;top:0;width:1200px;height:81px;background:#fff;box-shadow:0 1px 3px rgba(0,0,0,.15)}
.brand{position:absolute;left:99px;top:20px;display:flex;align-items:center;gap:8px;font-family:"Raleway",sans-serif;font-weight:800;font-size:34px;color:var(--brand);letter-spacing:1px}
.brand-dot{width:14px;height:14px;border-radius:50%;background:var(--brand)}
.nav{position:absolute;right:99px;top:24px;display:flex;align-items:center;font-family:"Raleway",sans-serif;font-weight:500;font-size:16px;color:#333}
.nav a{color:inherit;text-decoration:none;margin-left:44px;line-height:34px}
.nav .nav-cta{background:var(--brand);color:#fff;padding:0 10px;margin-left:34px}
.nav .nav-user{margin-left:35px}
.booking-card{position:absolute;left:99px;top:151px;width:1003px;height:363px;background:#fff;border-top:4px solid var(--brand);box-shadow:0 0 2px rgba(0,0,0,.08)}
.section-title{font-family:"Raleway",sans-serif;font-weight:500;font-size:29px;text-align:center;color:var(--ink);letter-spacing:.3px}
.section-title b{font-weight:800}
.booking-card .section-title{position:absolute;left:0;right:0;top:40px}
.field-label{position:absolute;font-size:13px;color:var(--muted)}
.field{position:absolute;height:35px;border:1px solid var(--line);font-size:12.5px;color:#777;padding:0 13px;line-height:33px;background:#fff}
.field-addon{position:absolute;right:0;top:0;width:36px;height:33px;border-left:1px solid var(--line);display:flex;align-items:center;justify-content:center}
.btn-update{position:absolute;left:56px;top:280px;width:103px;height:41px;border-radius:21px;background:var(--brand);color:#fff;font-weight:600;font-size:15px;letter-spacing:.5px;display:flex;align-items:center;justify-content:center}
.drivers-title{position:absolute;left:0;width:1200px;top:574px}
.drivers{position:absolute;left:99px;top:644px;width:1003px;border:1px solid #9aa;background:#fff}
.notice{height:48px;background:var(--notice);font-size:16px;padding-left:36px;line-height:44px;color:#2b2b2b}
table{border-collapse:collapse;width:1001px;table-layout:fixed}
th{background:var(--table-head);color:#fff;font-family:"Raleway",sans-serif;font-weight:600;font-size:15.5px;text-align:left;height:58px;padding-left:29px}
td{height:58px;font-size:12.5px;color:#444;padding-left:29px;border-top:1px solid #b9c3c7;border-left:1px solid #b9c3c7}
td:first-child{border-left:none}
tr.alt td{background:var(--row-alt)}
th.sep{border-left:1px solid #5aa6c6}
td.status,td.action{padding-left:0;text-align:center}
.badge{display:inline-block;width:135px;height:34px;line-height:34px;color:#fff;font-weight:600;font-size:13px;letter-spacing:.4px}
.badge.accepted{background:var(--accepted)}
.badge.sent{background:var(--sent)}
.badge.pending{background:var(--pending)}
.btn-pay{display:inline-block;width:139px;height:44px;line-height:44px;background:var(--brand);color:#fff;font-weight:600;font-size:14.5px;letter-spacing:.3px}
.site-footer{position:absolute;left:0;width:1200px;top:1027px;text-align:center;font-size:12.5px;color:#333}
</style>
</head>
<body>
<header class="site-header">
  <div class="brand"><span class="brand-dot"></span>HAULVEX</div>
  <nav class="nav">
    <a href="#">Book</a>
    <a href="#">How it Works</a>
    <a href="#" class="nav-cta">Become a Driver</a>
    <a href="#" class="nav-user">morgan@trelvane.com</a>
  </nav>
</header>

<section class="booking-card">
  <h1 class="section-title">BOOKING <b>DETAILS</b></h1>
  <label class="field-label" style="left:56px;top:115px">Package Selected:</label>
  <div class="field" style="left:57px;top:139px;width:427px">Package 1
    <span class="field-addon"><svg width="10" height="14" viewBox="0 0 10 14"><path d="M1 6 5 1 9 6Z M1 8 5 13 9 8Z" fill="#888"/></svg></span>
  </div>
  <label class="field-label" style="left:518px;top:115px">Pick-up time Selected:</label>
  <div class="field" style="left:519px;top:139px;width:427px">July 18 at 4:13 am
    <span class="field-addon"><svg width="13" height="13" viewBox="0 0 13 13"><rect x="1" y="2" width="11" height="10" fill="none" stroke="#999"/><path d="M1 5H12M4 1V3M9 1V3M4 7H5M6 7H7M8 7H9M4 9H5M6 9H7M8 9H9" stroke="#999"/></svg></span>
  </div>
  <label class="field-label" style="left:56px;top:202px">Description:</label>
  <div class="field" style="left:57px;top:221px;width:888px">1 large stove</div>
  <div class="btn-update">UPDATE</div>
</section>

<h2 class="section-title drivers-title">DRIVERS IN <b>YOUR AREA</b></h2>

<section class="drivers">
  <div class="notice">Please stay on this page and be patient, While we contact the drivers and find you one ASAP.</div>
  <table>
    <colgroup><col style="width:171px"><col style="width:171px"><col style="width:274px"><col style="width:189px"><col style="width:196px"></colgroup>
    <thead><tr><th>NAME</th><th>DISTANCE (KM)</th><th>AGREED PICK-UP TIME</th><th class="sep"></th><th class="sep"></th></tr></thead>
    <tbody>
      <tr><td>Dale Brenner</td><td>4.04km away</td><td>July 18 at 4:13 am</td><td class="status"><span class="badge accepted">TIME ACCEPTED</span></td><td class="action"><span class="btn-pay">MAKE PAYMENT</span></td></tr>
      <tr class="alt"><td>Owen Parrish</td><td>5.7km away</td><td>-</td><td class="status"><span class="badge sent">REQUEST SENT</span></td><td class="action"></td></tr>
      <tr><td>Colin Marsh</td><td>11.13km away</td><td>-</td><td class="status"><span class="badge sent">REQUEST SENT</span></td><td class="action"></td></tr>
      <tr class="alt"><td>Reid Calloway</td><td>11.91km away</td><td>-</td><td class="status"><span class="badge pending">PENDING</span></td><td class="action"></td></tr>
    </tbody>
  </table>
</section>

<footer class="site-footer">Copyrights © 2017, Haulvex . All Rights Reserved.</footer>
</body>
</html>
```